Online Shop - Website Design for up an coming art studio

We require a fully functional website design - not just design - but complete coded online shop website please, which should be a word press style frame work to allow ease up updating the site in the future. The website will sell art work from up and coming artists. The business is called "Brindle Harbor Studios". I have attached our logo to allow the submitted designs to tie in with this.

Industry/Entity Type

Shop

Coding

Coded - Design and coding required

Number of Pages Required

1 page

Colors

Designer to choose colors to be used in the design.

Requirements
Must have
• The website design must incorporate and fully functional online eCommerce shop feature.

```html
<!DOCTYPE html>
<html lang="en">
<head>
<meta charset="utf-8">
<title>Brindle Harbor Studios</title>
<link href="https://fonts.googleapis.com/css2?family=Montserrat:wght@400;500;600;700&family=Lato:wght@400;700;900&display=swap" rel="stylesheet">
<style>
:root{
  --ink:#1b1b1b;
  --text:#555;
  --accent:#d3203a;
  --blue:#2b93d1;
  --footer:#454545;
  --footer-line:#6a6a6a;
  --white:#fff;
  --frame:#111;
}
*{box-sizing:border-box;margin:0;padding:0}
html,body{width:1200px;height:3015px;overflow:hidden;background:var(--white)}
body{position:relative;font-family:"Lato",sans-serif;color:var(--ink)}
.abs{position:absolute}

/* header */
.brand{left:96px;top:48px;display:flex;align-items:center;gap:12px}
.brand-mark{width:46px;height:46px;border-radius:50%;background:var(--ink);flex:none}
.brand-name{font-family:"Montserrat",sans-serif;font-weight:600;font-size:17px;letter-spacing:.4px;color:var(--ink);white-space:nowrap}
.search{left:614px;top:30px;width:306px;height:40px;border:1px solid #555;display:flex;align-items:center;justify-content:space-between;padding:0 12px;font-size:14px;color:#333}
.cart{left:950px;top:32px;display:flex;gap:12px;align-items:center}
.cart-text{font-size:13px;line-height:19px;color:#333}
.nav{left:394px;top:112px;display:flex;gap:38px;font-family:"Montserrat",sans-serif;font-size:14.5px;font-weight:500;letter-spacing:.4px}
.nav a{color:var(--ink);text-decoration:none}
.nav a.current{color:var(--accent)}

/* hero */
.hero{left:0;top:162px;width:1200px;height:514px;
  background:
    radial-gradient(ellipse 380px 300px at 880px 200px,rgba(170,90,70,.55),transparent 70%),
    radial-gradient(ellipse 260px 160px at 420px 110px,rgba(240,170,110,.45),transparent 70%),
    radial-gradient(ellipse 300px 200px at 560px 420px,rgba(90,70,110,.5),transparent 70%),
    linear-gradient(180deg,#7a6068 0%,#54465a 45%,#3a2f3c 100%)}
.hero-title{left:98px;top:248px;font-family:"Montserrat",sans-serif;color:var(--white);font-weight:700;font-size:48px;line-height:56px;letter-spacing:.5px}
.hero-title span{display:block;font-size:40px;font-weight:600}
.hero-copy{left:98px;top:382px;width:500px;color:var(--white);font-size:15px;line-height:27px}
.btn-outline{border:2px solid var(--white);color:var(--white);font-family:"Montserrat",sans-serif;font-size:14px;display:flex;align-items:center;justify-content:center}
.hero-btn{left:98px;top:468px;width:132px;height:54px}
.dots{left:98px;top:558px;display:flex;gap:8px}
.dots i{width:15px;height:15px;border-radius:50%;background:#aaa;display:block}
.dots i.on{background:var(--accent);border:2px solid #fff}

/* category tiles */
.tile{top:742px;width:486px;height:214px;border:9px solid var(--frame);border-bottom-width:12px}
.tile-fill{position:absolute;inset:0}
.tile-label{position:absolute;font-family:"Lato",sans-serif;font-weight:900;font-size:31px;line-height:46px;color:var(--white)}

/* section heads */
.section-head{left:0;width:1200px;text-align:center;font-family:"Montserrat",sans-serif;font-weight:500;font-size:24px;letter-spacing:.5px}
.section-rule{left:559px;width:82px;height:2px;background:var(--ink)}
.arrow{width:44px;height:44px}

/* product cards */
.product{top:1150px;width:240px;height:348px;background:var(--frame);padding:12px}
.product-art{width:216px;height:212px;background:var(--white);padding:16px}
.product-art div{width:100%;height:100%}
.product-info{background:var(--white);height:110px;margin-top:2px;text-align:center;padding-top:20px}
.product-name{font-size:16px;font-weight:700;letter-spacing:.3px}
.product-row{display:flex;align-items:center;justify-content:center;gap:4px;margin-top:20px}
.price{font-size:17px;margin-right:8px}
.price.sale{color:var(--accent);font-weight:700}
.icon-btn{width:30px;height:30px}

/* oil painting band */
.band{left:0;top:1572px;width:1200px;height:440px;
  background:
    radial-gradient(ellipse 260px 240px at 960px 260px,rgba(220,200,185,.55),transparent 70%),
    linear-gradient(90deg,#3b2a22 0%,#5b4232 40%,#8a6a4f 70%,#6b5040 100%)}
.band-panel{left:98px;top:1636px;width:606px;height:318px;background:rgba(43,147,209,.92);text-align:center;color:var(--white)}
.band-title{font-family:"Montserrat",sans-serif;font-weight:600;font-size:32px;margin-top:40px;letter-spacing:.5px}
.band-copy{font-size:14px;line-height:27px;font-weight:700;width:560px;margin:20px auto 0}
.band-btn{width:118px;height:46px;margin:24px auto 0;font-size:12.5px}

/* featured */
.feature{top:2176px;width:240px;height:236px;background:var(--frame);padding:12px 12px 16px}
.feature-art{width:100%;height:100%;background:var(--white);padding:16px}
.feature-art div{width:100%;height:100%}
.feature-caption{top:2440px;width:240px;text-align:center}
.feature-caption h3{font-family:"Montserrat",sans-serif;font-weight:500;font-size:17px;letter-spacing:.5px}
.feature-caption p{font-size:13px;line-height:21px;color:var(--text);margin-top:6px}

/* footer */
.footer{left:0;top:2566px;width:1200px;height:449px;background:var(--footer);border-top:5px solid var(--accent)}
.foot-brand{left:96px;top:2752px;display:flex;align-items:center;gap:12px}
.foot-brand .brand-mark{width:52px;height:52px;background:var(--white)}
.foot-brand .brand-name{color:var(--white);font-size:19px}
.contact-title{left:398px;top:2640px;color:var(--white);font-family:"Montserrat",sans-serif;font-weight:600;font-size:17px}
.contact-item{left:398px;display:flex;gap:18px;color:var(--white)}
.contact-item svg{flex:none}
.contact-item b{display:block;font-size:14px;font-weight:700;margin-bottom:4px}
.contact-item span{font-size:12.5px;line-height:19px}
.map{left:718px;top:2622px;width:380px;height:260px;background:linear-gradient(135deg,#efeee8,#dedcd2)}
.map-pin{left:900px;top:2712px}
.foot-rule{left:98px;top:2928px;width:1000px;height:1px;background:var(--footer-line)}
.copyright{left:98px;top:2962px;color:var(--white);font-size:13.5px;font-weight:700}
.socials{left:948px;top:2952px;display:flex;gap:10px}
.socials i{width:32px;height:32px;border:2px solid var(--white);border-radius:50%;display:block}
</style>
</head>
<body>

<header>
  <div class="abs brand">
    <div class="brand-mark"></div>
    <div class="brand-name">Brindle Harbor Studios</div>
  </div>
  <div class="abs search">Search
    <svg width="14" height="14" viewBox="0 0 14 14"><circle cx="6" cy="6" r="4.5" fill="none" stroke="#333" stroke-width="1.6"/><line x1="9.3" y1="9.3" x2="13" y2="13" stroke="#333" stroke-width="1.8"/></svg>
  </div>
  <div class="abs cart">
    <svg width="38" height="36" viewBox="0 0 38 36"><path d="M12 12V8a7 7 0 0 1 14 0v4" fill="none" stroke="#d3203a" stroke-width="2.5"/><rect x="4" y="12" width="30" height="22" rx="3" fill="#d3203a"/></svg>
    <div class="cart-text">Shopping Cart:<br>0 item(s) - $0.00</div>
  </div>
  <nav class="abs nav">
    <a class="current" href="#">HOME</a><a href="#">THE ARTWORKS</a><a href="#">ARTISTS</a><a href="#">PORTRAITS</a><a href="#">HOW DO I BUY ?</a><a href="#">CONTACT</a>
  </nav>
</header>

<section>
  <div class="abs hero" role="img" aria-label="Young artist painting a watercolour above a city at dusk"></div>
  <h1 class="abs hero-title">BRINDLE HARBOR<span>STUDIOS</span></h1>
  <p class="abs hero-copy">Nemo enim ipsam voluptatem quia voluptas sit aspernatur aut odit aut fugit, sed quia consequuntur magni dolores.</p>
  <div class="abs btn-outline hero-btn">READ MORE</div>
  <div class="abs dots"><i class="on"></i><i></i><i></i><i></i><i></i></div>
</section>

<section>
  <div class="abs tile" style="left:100px">
    <div class="tile-fill" role="img" aria-label="Paint brushes and palette knife on a palette" style="background:radial-gradient(ellipse 160px 120px at 110px 60px,rgba(210,170,110,.6),transparent 70%),linear-gradient(90deg,#6a5438,#8c7a6a 45%,#4a6aa8)"></div>
    <div class="tile-label" style="right:22px;top:70px;text-align:right">NEW<br>ARTWORKS</div>
  </div>
  <div class="abs tile" style="left:612px">
    <div class="tile-fill" role="img" aria-label="Jar of paint brushes" style="background:radial-gradient(ellipse 160px 130px at 360px 90px,rgba(225,205,170,.6),transparent 70%),linear-gradient(90deg,#3e5a3a,#6a7a56 50%,#b8a88a)"></div>
    <div class="tile-label" style="left:22px;top:70px">UPCOMING<br>ARTISTS</div>
  </div>
</section>

<section>
  <svg class="abs arrow" style="left:98px;top:1038px" viewBox="0 0 44 44"><circle cx="22" cy="22" r="20" fill="none" stroke="#222" stroke-width="1.6"/><path d="M25 14l-8 8 8 8" fill="none" stroke="#222" stroke-width="2"/></svg>
  <h2 class="abs section-head" style="top:1043px">POPULAR ARTWORKS</h2>
  <div class="abs section-rule" style="top:1094px"></div>
  <svg class="abs arrow" style="left:1056px;top:1038px" viewBox="0 0 44 44"><circle cx="22" cy="22" r="20" fill="none" stroke="#222" stroke-width="1.6"/><path d="M19 14l8 8-8 8" fill="none" stroke="#222" stroke-width="2"/></svg>

  <div class="abs product" style="left:102px">
    <div class="product-art"><div role="img" aria-label="Cubist painting of musicians" style="background:radial-gradient(circle at 70% 35%,rgba(200,60,40,.5),transparent 55%),linear-gradient(135deg,#d8b080,#a0603a 55%,#4a3428)"></div></div>
    <div class="product-info"><div class="product-name">CRAS NEQUE METUS</div>
      <div class="product-row"><span class="price sale">$122.50</span>
        <svg class="icon-btn" viewBox="0 0 30 30"><circle cx="15" cy="15" r="14" fill="#d3203a"/><path d="M8 10h2l2 8h8l2-6H11" fill="none" stroke="#fff" stroke-width="1.6"/><circle cx="13" cy="21" r="1.3" fill="#fff"/><circle cx="19" cy="21" r="1.3" fill="#fff"/></svg>
        <svg class="icon-btn" viewBox="0 0 30 30"><circle cx="15" cy="15" r="13.5" fill="none" stroke="#222" stroke-width="1.4"/><path d="M15 21l-5.5-5.5a3.2 3.2 0 0 1 5.5-3.5 3.2 3.2 0 0 1 5.5 3.5z" fill="none" stroke="#222" stroke-width="1.4"/></svg>
        <svg class="icon-btn" viewBox="0 0 30 30"><circle cx="15" cy="15" r="13.5" fill="none" stroke="#222" stroke-width="1.4"/><path d="M9 13h11l-3-3M21 17H10l3 3" fill="none" stroke="#222" stroke-width="1.4"/></svg>
      </div></div>
  </div>
  <div class="abs product" style="left:354px">
    <div class="product-art"><div role="img" aria-label="Hand painting a green landscape" style="background:radial-gradient(circle at 72% 62%,rgba(160,200,130,.7),transparent 55%),linear-gradient(135deg,#8a5a2a,#c0a060 45%,#90b070)"></div></div>
    <div class="product-info"><div class="product-name">CRAS NEQUE METUS</div>
      <div class="product-row"><span class="price">$122.50</span>
        <svg class="icon-btn" viewBox="0 0 30 30"><circle cx="15" cy="15" r="13.5" fill="none" stroke="#222" stroke-width="1.4"/><path d="M8 10h2l2 8h8l2-6H11" fill="none" stroke="#222" stroke-width="1.6"/><circle cx="13" cy="21" r="1.3" fill="#222"/><circle cx="19" cy="21" r="1.3" fill="#222"/></svg>
        <svg class="icon-btn" viewBox="0 0 30 30"><circle cx="15" cy="15" r="13.5" fill="none" stroke="#222" stroke-width="1.4"/><path d="M15 21l-5.5-5.5a3.2 3.2 0 0 1 5.5-3.5 3.2 3.2 0 0 1 5.5 3.5z" fill="none" stroke="#222" stroke-width="1.4"/></svg>
        <svg class="icon-btn" viewBox="0 0 30 30"><circle cx="15" cy="15" r="13.5" fill="none" stroke="#222" stroke-width="1.4"/><path d="M9 13h11l-3-3M21 17H10l3 3" fill="none" stroke="#222" stroke-width="1.4"/></svg>
      </div></div>
  </div>
  <div class="abs product" style="left:606px">
    <div class="product-art"><div role="img" aria-label="Painting of a canal with gondola" style="background:linear-gradient(180deg,#9cc4c0 0%,#d8c070 35%,#c89a4a 55%,#3a7a7a 80%,#2a5a5a 100%)"></div></div>
    <div class="product-info"><div class="product-name">CRAS NEQUE METUS</div>
      <div class="product-row"><span class="price">$122.50</span>
        <svg class="icon-btn" viewBox="0 0 30 30"><circle cx="15" cy="15" r="13.5" fill="none" stroke="#222" stroke-width="1.4"/><path d="M8 10h2l2 8h8l2-6H11" fill="none" stroke="#222" stroke-width="1.6"/><circle cx="13" cy="21" r="1.3" fill="#222"/><circle cx="19" cy="21" r="1.3" fill="#222"/></svg>
        <svg class="icon-btn" viewBox="0 0 30 30"><circle cx="15" cy="15" r="13.5" fill="none" stroke="#222" stroke-width="1.4"/><path d="M15 21l-5.5-5.5a3.2 3.2 0 0 1 5.5-3.5 3.2 3.2 0 0 1 5.5 3.5z" fill="none" stroke="#222" stroke-width="1.4"/></svg>
        <svg class="icon-btn" viewBox="0 0 30 30"><circle cx="15" cy="15" r="13.5" fill="none" stroke="#222" stroke-width="1.4"/><path d="M9 13h11l-3-3M21 17H10l3 3" fill="none" stroke="#222" stroke-width="1.4"/></svg>
      </div></div>
  </div>
  <div class="abs product" style="left:858px">
    <div class="product-art"><div role="img" aria-label="Painting of flowers by the sea" style="background:radial-gradient(circle at 65% 65%,rgba(240,200,60,.85),transparent 40%),radial-gradient(circle at 20% 85%,rgba(210,60,60,.8),transparent 40%),linear-gradient(180deg,#a8d4f0,#5aa8dc 50%,#d8e4ea)"></div></div>
    <div class="product-info"><div class="product-name">CRAS NEQUE METUS</div>
      <div class="product-row"><span class="price">$122.50</span>
        <svg class="icon-btn" viewBox="0 0 30 30"><circle cx="15" cy="15" r="13.5" fill="none" stroke="#222" stroke-width="1.4"/><path d="M8 10h2l2 8h8l2-6H11" fill="none" stroke="#222" stroke-width="1.6"/><circle cx="13" cy="21" r="1.3" fill="#222"/><circle cx="19" cy="21" r="1.3" fill="#222"/></svg>
        <svg class="icon-btn" viewBox="0 0 30 30"><circle cx="15" cy="15" r="13.5" fill="none" stroke="#222" stroke-width="1.4"/><path d="M15 21l-5.5-5.5a3.2 3.2 0 0 1 5.5-3.5 3.2 3.2 0 0 1 5.5 3.5z" fill="none" stroke="#222" stroke-width="1.4"/></svg>
        <svg class="icon-btn" viewBox="0 0 30 30"><circle cx="15" cy="15" r="13.5" fill="none" stroke="#222" stroke-width="1.4"/><path d="M9 13h11l-3-3M21 17H10l3 3" fill="none" stroke="#222" stroke-width="1.4"/></svg>
      </div></div>
  </div>
</section>

<section>
  <div class="abs band" role="img" aria-label="Artist in a white coat painting at an easel in a studio"></div>
  <div class="abs band-panel">
    <h2 class="band-title">OIL PAINTING</h2>
    <p class="band-copy">Nemo enim ipsam voluptatem quia voluptas sit aspernatur aut odit aut fugit, sed quia consequuntur magni dolores eos qui ratione voluptatem sequi nesciunt. Neque porro quisquam est, qui dolorem ipsum quia dolor sit amet, consectetur.</p>
    <div class="btn-outline band-btn">READ MORE</div>
  </div>
</section>

<section>
  <svg class="abs arrow" style="left:98px;top:2080px" viewBox="0 0 44 44"><circle cx="22" cy="22" r="20" fill="none" stroke="#222" stroke-width="1.6"/><path d="M25 14l-8 8 8 8" fill="none" stroke="#222" stroke-width="2"/></svg>
  <h2 class="abs section-head" style="top:2085px">FEATURED ARTWORKS</h2>
  <div class="abs section-rule" style="top:2136px"></div>
  <svg class="abs arrow" style="left:1056px;top:2080px" viewBox="0 0 44 44"><circle cx="22" cy="22" r="20" fill="none" stroke="#222" stroke-width="1.6"/><path d="M19 14l8 8-8 8" fill="none" stroke="#222" stroke-width="2"/></svg>

  <div class="abs feature" style="left:100px"><div class="feature-art"><div role="img" aria-label="Painting of a canal street" style="background:radial-gradient(circle at 40% 30%,rgba(250,230,160,.7),transparent 50%),linear-gradient(135deg,#d8c88a,#8a7a4a 55%,#3a3a2a)"></div></div></div>
  <div class="abs feature" style="left:354px"><div class="feature-art"><div role="img" aria-label="Painting of a flowered terrace by the sea" style="background:radial-gradient(circle at 25% 80%,rgba(220,80,60,.6),transparent 40%),linear-gradient(180deg,#8ab8d8,#e8e0c8 50%,#c8a06a)"></div></div></div>
  <div class="abs feature" style="left:606px"><div class="feature-art"><div role="img" aria-label="Painting of an ancient amphitheatre at night" style="background:radial-gradient(ellipse at 50% 50%,rgba(250,190,60,.9),transparent 55%),linear-gradient(180deg,#1a2a6a,#c87a2a 55%,#3a6ac8)"></div></div></div>
  <div class="abs feature" style="left:858px"><div class="feature-art"><div role="img" aria-label="Painting of an autumn street with a clock tower" style="background:radial-gradient(circle at 75% 55%,rgba(240,140,40,.7),transparent 45%),linear-gradient(180deg,#e8c49a,#d86a2a 55%,#6a3a2a)"></div></div></div>

  <div class="abs feature-caption" style="left:100px"><h3>MODERN PAINTING</h3><p>Nemo enim ipsam voluptatema<br>voluptas sit aspern</p></div>
  <div class="abs feature-caption" style="left:354px"><h3>MODERN ARTWORKS</h3><p>Nemo enim ipsam voluptatema<br>voluptas sit aspern</p></div>
  <div class="abs feature-caption" style="left:606px"><h3>MODERN PAINTING</h3><p>Nemo enim ipsam voluptatema<br>voluptas sit aspern</p></div>
  <div class="abs feature-caption" style="left:858px"><h3>MODERN ARTWORKS</h3><p>Nemo enim ipsam voluptatema<br>voluptas sit aspern</p></div>
</section>

<footer>
  <div class="abs footer"></div>
  <div class="abs foot-brand">
    <div class="brand-mark"></div>
    <div class="brand-name">Brindle Harbor Studios</div>
  </div>
  <h3 class="abs contact-title">CONTACT US</h3>
  <div class="abs contact-item" style="top:2690px">
    <svg width="38" height="38" viewBox="0 0 38 38"><circle cx="19" cy="19" r="17.5" fill="none" stroke="#fff" stroke-width="1.6"/><path d="M19 28s-6-7-6-11a6 6 0 0 1 12 0c0 4-6 11-6 11z" fill="#fff"/><circle cx="19" cy="17" r="2.2" fill="#454545"/></svg>
    <div><b>ADDRESS,</b><span>42 Larkfield Lane, Millbrook,<br>Westshire, Scotland, WS4 7QL</span></div>
  </div>
  <div class="abs contact-item" style="top:2776px">
    <svg width="38" height="38" viewBox="0 0 38 38"><circle cx="19" cy="19" r="17.5" fill="none" stroke="#fff" stroke-width="1.6"/><rect x="14" y="10" width="10" height="18" rx="2" fill="none" stroke="#fff" stroke-width="1.8"/><line x1="17" y1="25" x2="21" y2="25" stroke="#fff" stroke-width="1.5"/></svg>
    <div><b>PHONE:</b><span>190 044 7812</span></div>
  </div>
  <div class="abs contact-item" style="top:2840px">
    <svg width="38" height="38" viewBox="0 0 38 38"><circle cx="19" cy="19" r="17.5" fill="none" stroke="#fff" stroke-width="1.6"/><rect x="11" y="13" width="16" height="12" fill="#fff"/><path d="M11 13l8 6 8-6" fill="none" stroke="#454545" stroke-width="1.4"/></svg>
    <div><b>Mail:</b><span>hello@brindleharborstudios.com</span></div>
  </div>
  <div class="abs map" role="img" aria-label="Street map showing the studio location"></div>
  <svg class="abs map-pin" width="16" height="22" viewBox="0 0 16 22"><path d="M8 21S1 12.5 1 8a7 7 0 0 1 14 0c0 4.5-7 13-7 13z" fill="#d3203a"/><circle cx="8" cy="8" r="2.5" fill="#fff"/></svg>
  <div class="abs foot-rule"></div>
  <p class="abs copyright">Copyright © 2017 Brindle Harbor Studios. All Right Reserved</p>
  <div class="abs socials" aria-label="Social links"><i></i><i></i><i></i><i></i></div>
</footer>

</body>
</html>
```